Design and Renovation Company Luxury Business Card

I want to create a luxury business card for a Design and Renovation Firm . We will use our current logo. The company name is 528BUILDA. We do not want anything standard. We need a very unique concept.
Please see uploaded inspiration. I really like the textured paper option. I would like the card to be thick with debossing, and/or embossing options. The logo has orange in it but I would like to see the card with and without the orange. I think the orange may make the company feel less high-end. The goal is to elevate the logo not match its vibe per se of the logo. We want something very unique, not standard at all!
I would like a space for :
Logo,
Name,
Position,
Email,
Office number,
Website Address,
Business Address,
Thank you!
Have fun!
Target Market(s)
Home owners Age 35 +
Industry/Entity Type
Design and Renovation
Contact Information for Business Card
Logo, Name, Position, Email, Office number, Website Address, Business Address,.
Colors
Designer to choose colors to be used in the design.
Requirements
Must have
- A luxury designer feel. Must be black or dark grey but open to other luxury ideas.
Nice to have
- Gold, silver, black embossing or debossing. Textured paper design.
Should not have
- A cheap look and feel.

```html
<!DOCTYPE html>
<html lang="en">
<head>
<meta charset="utf-8">
<title>528BUILDA Business Card</title>
<link rel="stylesheet" href="https://fonts.googleapis.com/css2?family=Arimo:wght@400;700&display=swap">
<style>
  :root {
    --backdrop: #dcdcdc;
    --card-dark: #323232;
    --accent: #e8861e;
    --accent-deep: #d9701a;
    --ink-light: #ffffff;
  }
  * { margin: 0; padding: 0; box-sizing: border-box; }
  html, body { width: 1200px; height: 800px; overflow: hidden; }
  body {
    background: var(--backdrop);
    font-family: "Arimo", Arial, sans-serif;
    position: relative;
  }
  .card {
    position: absolute;
    top: 245px;
    width: 540px;
    height: 310px;
    border-radius: 22px;
    overflow: hidden;
  }
  .card-front { left: 40px; background: var(--card-dark); }
  .card-back { left: 620px; }

  .company-name {
    position: absolute; left: 290px; top: 100px;
    font-weight: 700; font-size: 32px; line-height: 40px;
    color: var(--ink-light); white-space: nowrap;
  }
  .name-band {
    position: absolute; left: 0; top: 150px;
    width: 272px; height: 12px; background: var(--ink-light);
  }
  .person-name {
    position: absolute; left: 34px; top: 122px;
    font-weight: 700; font-size: 22px; color: var(--accent);
  }
  .person-role {
    position: absolute; left: 52px; top: 168px;
    font-size: 14px; color: var(--ink-light);
  }
  .address {
    position: absolute; left: 52px; top: 200px;
    font-style: normal;
    font-size: 13px; line-height: 18px; color: var(--ink-light);
  }
  .contacts {
    position: absolute; left: 52px; top: 244px;
    list-style: none; font-size: 13px; line-height: 18px; color: var(--ink-light);
  }
  .contacts li { display: flex; align-items: center; gap: 8px; }
  .contacts svg { width: 11px; height: 11px; fill: var(--accent); flex: none; }

  .back-surface {
    position: absolute; inset: 0;
    background: linear-gradient(135deg, var(--accent) 0%, var(--accent-deep) 100%);
  }
  .back-brand {
    position: absolute; right: 40px; top: 166px;
    display: flex; align-items: center; gap: 10px;
  }
  .back-brand-square { width: 20px; height: 20px; background: var(--ink-light); }
  .back-brand-name {
    font-weight: 700; font-size: 22px; color: var(--ink-light);
  }
</style>
</head>
<body>
  <section class="card card-front">
    <div class="company-name">528BUILDA</div>
    <div class="name-band"></div>
    <div class="person-name">Marcus Hale</div>
    <div class="person-role">President</div>
    <address class="address">
      4127 Kingsbridge Lane<br>Cedar Grove, NY 11020
    </address>
    <ul class="contacts">
      <li><svg viewBox="0 0 12 12"><path d="M2.5 0.5 L4.5 0.5 L5 3.5 L3.6 4.4 Q4.8 7.2 7.6 8.4 L8.5 7 L11.5 7.5 L11.5 9.5 Q11.5 11.5 9.5 11.5 Q0.5 10.5 0.5 2.5 Q0.5 0.5 2.5 0.5 Z"/></svg>(614) 5290-3378</li>
      <li><svg viewBox="0 0 12 12"><path d="M0.5 2 H11.5 V10 H0.5 Z M1.2 2.6 L6 6.4 L10.8 2.6 Z" fill-rule="evenodd"/></svg>name@528BUILDA.com</li>
      <li><svg viewBox="0 0 12 12"><circle cx="6" cy="6" r="5.5"/></svg>www.528BUILDA.com</li>
    </ul>
  </section>

  <section class="card card-back">
    <div class="back-surface" role="img" aria-label="Embossed repeating square tile pattern in deeper orange tones"></div>
    <div class="back-brand">
      <div class="back-brand-square"></div>
      <div class="back-brand-name">528BUILDA</div>
    </div>
  </section>
</body>
</html>
```